KVM Contracting services . Building and maintenance services, optic fibre installation

Business cards and logo design.I need a logo that I can use on business cards ,workwear and on my vehicles. I would like the KVM to be the main or larger text and contracting services to be the smaller or less important text.I like monograms, modern designs and repeating patterns symbols. I am also a Gemini and my favourite number is 22 so if this can be any inspiration to help with the design. Am thinking of the using German flag colours as a his is my family’s heritage. And the other 2 main colours I wear is black and white.But any ideas are appreciated.I do not need a design that is trade specific but a design that could be used for any business.

Target Market(s)

General public

Contact Information for Business Card

KVM Contracting Services ( front of business card)

(Back of business card)
Darren Holtwick
0451907326
Maintenance services
Optic fibre and data installation

Logo Text

Logo can just be pattern or monogram or incorporate KVM . I like the gemini star sign and the number 22

Colors
ec1f27
000000
fbee3e
ffffff

Requirements
Must have
• Logo and KVM Contracting Services on the front of business card
Nice to have
• Possible use of German flag colours.
• Modern design.
• Design to be able to be used on black or white background as I want to put it on clothing

```html
<!DOCTYPE html>
<html lang="en">
<head>
<meta charset="utf-8">
<title>KVM Contracting Services – Business Cards</title>
<link rel="stylesheet" href="https://fonts.googleapis.com/css2?family=Lato:wght@400;700&display=swap">
<style>
  :root {
    --backdrop: #1c1c1c;
    --card: #222222;
    --card-edge: #2c2c2c;
    --red: #ec1f27;
    --white: #ffffff;
    --silver: #b9b9b9;
    --muted: #e6e6e6;
  }
  * { margin: 0; padding: 0; box-sizing: border-box; }
  html, body {
    width: 1200px; height: 900px; overflow: hidden;
    background: var(--backdrop);
    font-family: "Lato", Arial, sans-serif;
  }
  .canvas {
    position: relative; width: 1200px; height: 900px;
    display: flex; flex-direction: column; align-items: center; justify-content: center; gap: 40px;
  }
  .card {
    position: relative; width: 740px; height: 400px;
    background: linear-gradient(135deg, var(--card) 0%, var(--card-edge) 100%);
    box-shadow: 0 14px 30px rgba(0,0,0,.55);
  }
  /* Brand placeholder: plain square + name in one colour and weight */
  .brand { display: flex; align-items: center; gap: 16px; }
  .brand__mark { flex-shrink: 0; }
  .brand__name { font-weight: 700; line-height: 1.1; }

  /* Front */
  .card--front { display: flex; align-items: center; justify-content: center; }
  .card--front .brand__mark { width: 44px; height: 44px; background: var(--silver); }
  .card--front .brand__name { font-size: 42px; color: var(--silver); }

  /* Back */
  .card--back { display: flex; align-items: center; padding: 0 40px 0 48px; }
  .card--back .brand { width: 260px; flex-shrink: 0; align-items: flex-start; }
  .card--back .brand__mark { width: 30px; height: 30px; background: var(--red); margin-top: 4px; }
  .card--back .brand__name { font-size: 32px; color: var(--red); }
  .divider { width: 2px; height: 250px; background: var(--white); margin: 0 30px 0 22px; flex-shrink: 0; }
  .contact { color: var(--muted); font-size: 16px; line-height: 1.4; }
  .contact__name { color: var(--red); font-size: 24px; font-weight: 400; text-transform: uppercase; letter-spacing: .5px; line-height: 1.15; }
  .contact__role { margin-bottom: 10px; }
  .contact__services { margin-bottom: 10px; }
  .contact__address { margin-bottom: 10px; }
  .contact__line { display: flex; align-items: center; gap: 10px; }
  .contact__icon { width: 12px; height: 12px; flex-shrink: 0; }
</style>
</head>
<body>
<main class="canvas">
  <section class="card card--front" aria-label="Business card front">
    <div class="brand">
      <span class="brand__mark"></span>
      <span class="brand__name">KVM Contracting Services</span>
    </div>
  </section>

  <section class="card card--back" aria-label="Business card back">
    <div class="brand">
      <span class="brand__mark"></span>
      <span class="brand__name">KVM Contracting Services</span>
    </div>
    <div class="divider"></div>
    <div class="contact">
      <p class="contact__name">Darren Holtwick</p>
      <p class="contact__role">Director</p>
      <p class="contact__services">Maintenance services<br>Optic fibre and data installation</p>
      <p class="contact__address">118 Larkspur Ave,<br>Millbrook, FL 32099, USA</p>
      <p class="contact__line">
        <svg class="contact__icon" viewBox="0 0 12 12"><path d="M3 1 L5 3.5 L4 4.8 Q5 7 7.2 8 L8.5 7 L11 9 L9.8 11 Q3 10.5 1 2.2 Z" fill="var(--red)"/></svg>
        0451907326
      </p>
      <p class="contact__line">
        <svg class="contact__icon" viewBox="0 0 12 12"><rect x="1" y="2.5" width="10" height="7" fill="none" stroke="var(--red)" stroke-width="1.2"/><path d="M1 2.5 L6 6.5 L11 2.5" fill="none" stroke="var(--red)" stroke-width="1.2"/></svg>
        office@kvmbuildworks.com
      </p>
      <p class="contact__line">
        <svg class="contact__icon" viewBox="0 0 12 12"><circle cx="6" cy="6" r="5" fill="none" stroke="var(--red)" stroke-width="1.1"/><ellipse cx="6" cy="6" rx="2.2" ry="5" fill="none" stroke="var(--red)" stroke-width="1"/><path d="M1 6 H11" stroke="var(--red)" stroke-width="1"/></svg>
        www.kvmbuildworks.com
      </p>
    </div>
  </section>
</main>
</body>
</html>
```